Marrowind - IT Consultancy Website

Our company is called Marrowind and our purpose is to help companies sustainably embrace and reap the benefits of cloud platforms, through transforming practices, skills and technology using DevOps and Security practices such that they are able to automate, manage and secure their cloud platforms to deliver product to market with increasing velocity.

To get our business started I require a website that will model the typical layout of an IT consultancy services company to an Australian Market. There are many examples of such a site, here are some of them. We would like a landing page and then a few simple menu options (About, Blog, Services etc..) to additional content

http://pelvo.com.au/
http://www.brisket.com.au/
http://www.tandu.com.au/

I require the site to be created with a separate CSS file that maintains the colour palette. This is a very important requirement, I want to be able to change the colours employed in the site in a single location and not have to scan through multiple files to replace the codes.

The website must be built using static content as it will not be hosted on a web server but instead in QNT using S3 and CloudFront CDN. Therefore please stick to HTML, JavaScript, CSS and other static file formats. The website needs to be response, smooth and reactive. It should render on desktop, mobile and tablet and feature smooth scrolling, transitions and fade in's.

The website should give the customer confidence that they are dealing with a highly professional IT services company, focused strongly on cloud (QNT, Vantrel Skyline, Horvik Vapor etc..), motivated by beautiful and fluid design.

In order to make this simpler for you, the designer, I have already purchased this template from https://skinmarketly.com/theme/the-venture-allround-template-KX7Q41093 and uploaded it. Feel free to use this template if you choose (note that it makes use of a separate color palette which is a key requirement) or use one of your own choosing. If you do use this template ensure that it does not look too much like "another bootstrap site" therefore use the layout and widgets but make the site look fresh and original too.
Obviously you must delete all trace of the bootstrap package once the project has completed if you do use it

Target Market(s)

Corporate and medium enterprise businesses

Industry/Entity Type

Information Technology

Coding

Coded - Design and coding required

Number of Pages Required

4 page

Font styles to use
Sans Serif

Colors
abd036
33a6d7

Requirements
Must have
• The website should give the customer confidence that they are dealing with a highly professional IT services company, focused strongly on cloud (QNT, Vantrel Skyline, Horvik Vapor etc..), motivated by beautiful and fluid design. Our company name is Marrowind, the site needs to pay homage to the themes of fluidity and logic
• Along with About Us, Services and a Blog page could I also get social logo's included too
Nice to have
• The website must be built using static content as it will not be hosted on a web server but instead in QNT using S3 and CloudFront CDN. Therefore please stick to HTML, JavaScript, CSS and other static file formats. The website needs to be response, smooth and reactive. It should render on desktop, mobile and tablet and feature smooth scrolling, transitions and fade in's.
Should not have
• Lurid colours, or too much animations. The design must "flow"

```html
<!DOCTYPE html>
<html lang="en">
<head>
<meta charset="utf-8">
<title>Marrowind IT Consultancy</title>
<link rel="stylesheet" href="https://fonts.googleapis.com/css2?family=Open+Sans:ital,wght@0,400;0,600;0,700;1,400&family=Raleway:wght@500;600;700&display=swap">
<style>
:root{
  --blue:#2b8ad3;
  --blue-deep:#1d4f7c;
  --navy:#142a40;
  --navy-dark:#0d1c2b;
  --navy-input:#223d59;
  --box-dark:#1b3b5c;
  --text:#333333;
  --muted:#777777;
  --light:#f2f2f2;
  --line:#e3e3e3;
  --white:#ffffff;
  --head:"Raleway",sans-serif;
  --body:"Open Sans",sans-serif;
}
*{box-sizing:border-box;margin:0;padding:0}
html,body{width:1200px;height:3468px;overflow:hidden}
body{font-family:var(--body);color:var(--text);font-size:13px;line-height:1.7;background:var(--white);position:relative}
.abs{position:absolute}
h2,h3,h4{font-family:var(--head);font-weight:700;color:#222}
.read-more{font-size:12px;font-weight:700;color:var(--blue);letter-spacing:.3px;text-decoration:none}
.ticks{list-style:none}
.ticks li{display:flex;align-items:center;gap:10px;font-size:12.5px;color:#555;height:27px}
.ticks svg{flex:none}
.ph{display:block}

/* top bar */
.topbar{top:0;left:0;width:1200px;height:37px;background:var(--blue-deep)}
.topbar .socials{left:97px;top:9px;display:flex;gap:5px}
.topbar .socials span{width:19px;height:19px;background:var(--blue);border-radius:2px;display:flex;align-items:center;justify-content:center}
.topbar .contact{right:97px;top:8px;display:flex;gap:22px;font-size:11px;color:#fff;align-items:center}
.topbar .contact span{display:flex;gap:7px;align-items:center}

/* nav */
.nav{top:37px;left:0;width:1200px;height:74px;background:#fff}
.logo-name{font-family:var(--head);font-weight:700;font-size:27px;color:var(--blue);line-height:1}
.logo-sub{font-family:var(--head);font-weight:500;font-size:14px;color:var(--blue-deep);line-height:1.2;letter-spacing:.5px}
.nav .brand{left:97px;top:15px}
.nav .menu{top:26px;font-size:14.5px;color:#333}
.nav .menu.active{color:var(--blue)}

/* hero */
.hero{top:111px;left:0;width:1200px;height:479px;background:linear-gradient(180deg,#6ea6d6 0%,#b5cfe3 22%,#5a7a95 45%,#8c9aa3 62%,#2d6d92 78%,#1d5c82 100%)}
.hero-box{left:585px;top:150px;width:513px;height:178px;background:rgba(15,35,55,.72);padding:22px 28px}
.hero-box h1{font-family:var(--head);font-weight:700;color:#fff;font-size:32px;line-height:1.1;margin-bottom:12px}
.hero-box p{color:#e6eef5;font-size:14px;line-height:1.55;width:470px}
.hero-btn{position:absolute;right:24px;bottom:20px;border:1px solid #fff;color:#fff;font-size:11.5px;font-weight:700;padding:6px 14px}
.arrow{width:40px;height:56px;background:rgba(0,0,0,.45);display:flex;align-items:center;justify-content:center}

/* welcome */
.welcome h2{left:97px;top:640px;font-size:23px}
.welcome .copy{left:97px;top:685px;width:460px;font-size:11.5px;color:#666;line-height:1.75}
.welcome .copy p{margin-bottom:14px}

/* services */
.services{top:1040px;left:0;width:1200px;height:467px;background:var(--light)}
.sec-title{width:1200px;text-align:center;font-size:24px}
.card{top:100px;width:314px}
.card .ph{width:314px;height:205px;position:relative}
.card .label{position:absolute;left:0;bottom:0;width:100%;height:38px;background:rgba(20,30,40,.6);color:#fff;font-family:var(--head);font-weight:700;font-size:17px;padding:7px 14px}
.card p{font-size:11.5px;color:#666;margin-top:16px;line-height:1.75}
.card .read-more{display:block;margin-top:14px}

/* feature band */
.band{top:1507px;height:208px;background:var(--blue);color:#fff;padding:45px 0 0}
.band.dark{background:var(--box-dark)}
.band h3{font-family:var(--head);color:#fff;font-size:17px;display:flex;gap:10px;align-items:center;margin-bottom:10px}
.band p{font-size:11.5px;line-height:1.75;width:300px;color:#e8f2fb}
.band .read-more{color:#fff;display:block;margin-top:12px}

/* process */
.tabs{left:97px;top:1820px;display:flex;gap:26px;font-size:12.5px;color:#777}
.tabs span{display:flex;gap:7px;align-items:center}
.tabs .on{color:#333;text-decoration:underline}
.process h3{left:97px;top:1870px;font-size:17px}
.process .copy{left:97px;top:1910px;width:460px;font-size:11.5px;color:#666;line-height:1.75}
.process .copy p{margin-bottom:14px}
.video{left:610px;top:1836px;width:488px;height:333px;background:radial-gradient(circle at 50% 55%,#3b6f9a 0%,#1d3550 45%,#0c1522 100%);box-shadow:0 0 0 4px #eee}
.video .bar{position:absolute;top:0;left:0;width:100%;height:36px;background:rgba(0,0,0,.35);color:#fff;font-size:14px;font-weight:600;padding:7px 14px;display:flex;justify-content:space-between}
.video .play{position:absolute;left:214px;top:136px;width:60px;height:60px;border-radius:50%;background:rgba(0,0,0,.7);display:flex;align-items:center;justify-content:center}

/* testimonial */
.quote-band{top:2231px;left:0;width:1200px;height:335px;background:linear-gradient(90deg,#3c5d7c 0%,#7d98b0 35%,#9fb3c4 55%,#6d8aa6 80%,#2f4f6e 100%)}
.avatar{left:556px;top:52px;width:88px;height:88px;border-radius:50%;background:linear-gradient(#cfd6dc,#8897a4);border:4px solid #fff}
.quote-band .who{top:156px;width:1200px;text-align:center;color:#fff;font-family:var(--head);font-weight:700;font-size:16px}
.quote-band blockquote{top:195px;left:200px;width:800px;text-align:center;color:#eef3f8;font-size:12.5px;font-style:italic;line-height:1.85}
.quote-band cite{top:262px;width:1200px;text-align:center;color:#fff;font-style:normal;font-weight:700;font-size:14px}

/* why / news */
.why h2,.news h2{top:2622px;font-size:22px}
.why .intro{left:97px;top:2672px;width:420px;font-size:11.5px;color:#666;line-height:1.75}
.why .ticks{left:97px;top:2737px}
.why .ticks li{height:37px}
.news-item{left:587px;width:511px;height:119px}
.news-item .ph{width:151px;height:115px;position:absolute;left:0;top:0}
.news-item h4{position:absolute;left:176px;top:-4px;width:335px;font-family:var(--body);font-size:13.5px;line-height:1.45;text-transform:uppercase;text-decoration:underline;color:#222}
.news-item .meta{position:absolute;left:176px;top:42px;font-size:11px;color:var(--blue);display:flex;gap:12px;font-style:italic}
.news-item .meta span{display:flex;gap:5px;align-items:center}
.news-item p{position:absolute;left:176px;top:62px;width:335px;font-size:11.5px;color:#666;line-height:1.7}
.news .rule{left:587px;width:511px;height:1px;background:var(--line)}

/* footer */
.footer{top:3068px;left:0;width:1200px;height:338px;background:var(--navy);color:#d5dfe9}
.footer .brand{left:97px;top:45px}
.footer .brand .logo-name{color:#fff;font-size:24px}
.footer .brand .logo-sub{color:#fff;font-size:13px}
.footer .about{left:97px;top:108px;width:470px;font-size:11.5px;line-height:1.7;color:#fff}
.footer .reach{left:97px;top:190px;display:flex;gap:16px;font-size:11px;color:#fff;align-items:center}
.footer .reach span{display:flex;gap:8px;align-items:center}
.footer .reach i{width:1px;height:14px;background:#5d7690}
.footer .circles{left:97px;top:252px;display:flex;gap:24px}
.footer .circles span{width:34px;height:34px;border:1.5px solid #fff;border-radius:50%;display:flex;align-items:center;justify-content:center}
.footer h3{left:670px;top:40px;color:#fff;font-size:21px}
.field{left:670px;width:428px;background:var(--navy-input);color:#fff;font-size:11px;padding:6px 12px;display:flex;justify-content:space-between}
.send{left:670px;top:263px;width:74px;height:33px;background:var(--blue);color:#fff;font-size:12px;font-weight:700;display:flex;align-items:center;justify-content:center}
.copyright{top:3406px;left:0;width:1200px;height:62px;background:var(--navy-dark);color:#c9d4de;font-size:11px;text-align:center;padding-top:21px}
</style>
</head>
<body>

<header>
  <div class="abs topbar">
    <div class="abs socials">
      <span></span><span></span><span></span><span></span><span></span>
      <span><svg width="11" height="9" viewBox="0 0 11 9"><rect x=".5" y=".5" width="10" height="8" fill="none" stroke="#fff"/><path d="M.5 .5l5 4 5-4" fill="none" stroke="#fff"/></svg></span>
    </div>
    <div class="abs contact">
      <span><svg width="11" height="11" viewBox="0 0 12 12"><path d="M2 1l2.5 0 1 3-1.5 1c.7 1.5 1.5 2.3 3 3l1-1.5 3 1V10c0 .6-.5 1-1 1C5 11 1 7 1 2c0-.5.4-1 1-1z" fill="#fff"/></svg>1 888 888 888</span>
      <span><svg width="12" height="9" viewBox="0 0 11 9"><rect x=".5" y=".5" width="10" height="8" fill="none" stroke="#fff"/><path d="M.5 .5l5 4 5-4" fill="none" stroke="#fff"/></svg>info@marrowindconsultancy.com</span>
    </div>
  </div>

  <nav class="abs nav">
    <div class="abs brand"><div class="logo-name">Marrowind</div><div class="logo-sub">IT Consultancy</div></div>
    <span class="abs menu active" style="left:490px">Home</span>
    <span class="abs menu" style="left:564px">About Us</span>
    <span class="abs menu" style="left:661px">Services</span>
    <span class="abs menu" style="left:754px">Blog</span>
    <span class="abs menu" style="left:818px">News</span>
    <span class="abs menu" style="left:890px">Careers</span>
    <span class="abs menu" style="left:978px">Contact Us</span>
    <svg class="abs" style="left:1088px;top:31px" width="14" height="14" viewBox="0 0 14 14"><circle cx="6" cy="6" r="4.5" fill="none" stroke="#333" stroke-width="2"/><path d="M9.3 9.3L13 13" stroke="#333" stroke-width="2.2"/></svg>
  </nav>
</header>

<section class="abs hero" role="img" aria-label="Coastal city skyline with high-rise towers beside a beach and ocean">
  <div class="abs arrow" style="left:0;top:212px"><svg width="12" height="18" viewBox="0 0 12 18"><path d="M10 2L3 9l7 7" fill="none" stroke="#fff" stroke-width="2"/></svg></div>
  <div class="abs arrow" style="left:1160px;top:212px;border-radius:28px 0 0 28px"><svg width="12" height="18" viewBox="0 0 12 18"><path d="M2 2l7 7-7 7" fill="none" stroke="#fff" stroke-width="2"/></svg></div>
  <div class="abs hero-box">
    <h1>Marrowind IT Consultancy</h1>
    <p>We help companies sustainably embrace and reap the benefits of cloud platforms, through transforming practices, skills and technology using DevOps and Security practices.</p>
    <span class="hero-btn">GET MORE INFO &gt;&gt;</span>
  </div>
</section>

<section class="welcome">
  <h2 class="abs">Welcome to Marrowind IT Consultancy</h2>
  <div class="abs copy">
    <p>Lorem ipsum dolor sit amet, consectetur adipisicing elit. Temporibus illo vero cupiditate, sed enim voluptatibus provident consectetur.</p>
    <p>Blanditiis aspernatur, non quasi, maxime corporis officiis quia. Cupiditate, voluptatibus ducimus, natus, labore mollitia dolorem incidunt voluptatum, delectus eius git porro placeat animi voluptatem autem hic eligendi sint.</p>
    <ul class="ticks">
      <li><svg width="14" height="14" viewBox="0 0 14 14"><circle cx="7" cy="7" r="7" fill="#2b8ad3"/><path d="M3.8 7.2l2.2 2.2 4.2-4.4" fill="none" stroke="#fff" stroke-width="1.6"/></svg>We are here to support you</li>
      <li><svg width="14" height="14" viewBox="0 0 14 14"><circle cx="7" cy="7" r="7" fill="#2b8ad3"/><path d="M3.8 7.2l2.2 2.2 4.2-4.4" fill="none" stroke="#fff" stroke-width="1.6"/></svg>Free updates</li>
      <li><svg width="14" height="14" viewBox="0 0 14 14"><circle cx="7" cy="7" r="7" fill="#2b8ad3"/><path d="M3.8 7.2l2.2 2.2 4.2-4.4" fill="none" stroke="#fff" stroke-width="1.6"/></svg>Unlimited options and variations</li>
      <li><svg width="14" height="14" viewBox="0 0 14 14"><circle cx="7" cy="7" r="7" fill="#2b8ad3"/><path d="M3.8 7.2l2.2 2.2 4.2-4.4" fill="none" stroke="#fff" stroke-width="1.6"/></svg>Ipsam asperiores fugiat quo</li>
    </ul>
    <a class="read-more" style="display:block;margin-top:14px">READ MORE &gt;&gt;</a>
  </div>
  <div class="abs ph" style="left:610px;top:645px;width:488px;height:335px;background:radial-gradient(circle at 45% 45%,#3fa3e0 0%,#135082 45%,#08213d 100%)" role="img" aria-label="Hand touching glowing cloud computing network icons"></div>
</section>

<section class="abs services">
  <h2 class="abs sec-title" style="top:40px">Our Services</h2>
  <div class="abs card" style="left:97px">
    <div class="ph" style="background:linear-gradient(135deg,#8fd0f0,#2a8fcf 60%,#16507f)" role="img" aria-label="Digital padlock on a blue network background"><div class="label">QNT</div></div>
    <p>Nemo enim ipsam voluptatem quia voluptas sit aspernatur aut odit aut fugit, sed quia consequuntur magni dolores eos qui ratione voluptatem sequi.</p>
    <a class="read-more">READ MORE &gt;&gt;</a>
  </div>
  <div class="abs card" style="left:442px">
    <div class="ph" style="background:linear-gradient(135deg,#cfc9bd,#7d7a72 50%,#3a3c3a)" role="img" aria-label="Hand holding a smartphone showing a spreadsheet app"><div class="label">Vantrel Skyline</div></div>
    <p>Nemo enim ipsam voluptatem quia voluptas sit aspernatur aut odit aut fugit, sed quia consequuntur magni dolores eos qui ratione voluptatem sequi.</p>
    <a class="read-more">READ MORE &gt;&gt;</a>
  </div>
  <div class="abs card" style="left:788px">
    <div class="ph" style="background:linear-gradient(135deg,#4a5560,#252c33 55%,#0f1419)" role="img" aria-label="Person holding a tablet with a cloud hovering above"><div class="label">Horvik Vapor</div></div>
    <p>Nemo enim ipsam voluptatem quia voluptas sit aspernatur aut odit aut fugit, sed quia consequuntur magni dolores eos qui ratione voluptatem sequi.</p>
    <a class="read-more">READ MORE &gt;&gt;</a>
  </div>
</section>

<section class="features">
  <div class="abs band" style="left:0;width:412px;padding-left:97px">
    <h3><svg width="20" height="18" viewBox="0 0 20 18"><path d="M8 3H2v13h13v-5" fill="none" stroke="#fff" stroke-width="2"/><path d="M7 11c1-5 5-7 10-7M14 1l4 3-4 3" fill="none" stroke="#fff" stroke-width="2"/></svg>Transforming Practices</h3>
    <p>At vero eos et accusamus et iusto odio dignissimos ducimus qui blanditiis praesentium voluptatum deleniti atque corrupti quos dolores.</p>
    <a class="read-more">READ MORE &gt;&gt;</a>
  </div>
  <div class="abs band dark" style="left:412px;width:374px;padding-left:41px">
    <h3><svg width="22" height="18" viewBox="0 0 22 18"><circle cx="7" cy="9" r="4.5" fill="none" stroke="#fff" stroke-width="3" stroke-dasharray="2.2 1.3"/><circle cx="7" cy="9" r="2" fill="#fff"/><circle cx="17" cy="5" r="3" fill="none" stroke="#fff" stroke-width="2.4" stroke-dasharray="1.6 1"/></svg>DevOps</h3>
    <p>At vero eos et accusamus et iusto odio dignissimos ducimus qui blanditiis praesentium voluptatum deleniti atque corrupti quos dolores.</p>
    <a class="read-more">READ MORE &gt;&gt;</a>
  </div>
  <div class="abs band" style="left:786px;width:414px;padding-left:28px">
    <h3><svg width="16" height="19" viewBox="0 0 16 19"><path d="M4 8V5a4 4 0 018 0v3" fill="none" stroke="#fff" stroke-width="2"/><rect x="1" y="8" width="14" height="10" rx="1" fill="#fff"/></svg>Security practices</h3>
    <p>At vero eos et accusamus et iusto odio dignissimos ducimus qui blanditiis praesentium voluptatum deleniti atque corrupti quos dolores.</p>
    <a class="read-more">READ MORE &gt;&gt;</a>
  </div>
</section>

<section class="process">
  <h2 class="abs sec-title" style="top:1764px">The Process We Follow</h2>
  <div class="abs tabs">
    <span class="on"><svg width="12" height="12" viewBox="0 0 12 12"><circle cx="6" cy="6" r="5" fill="none" stroke="#555" stroke-width="1.5"/><circle cx="6" cy="6" r="2" fill="#555"/></svg>Step 1 &gt;&gt;</span>
    <span><svg width="12" height="12" viewBox="0 0 12 12"><circle cx="6" cy="6" r="5" fill="none" stroke="#888" stroke-width="1.5"/><circle cx="6" cy="6" r="2" fill="#888"/></svg>Step 2 &gt;&gt;</span>
    <span><svg width="12" height="12" viewBox="0 0 12 12"><circle cx="6" cy="6" r="5" fill="none" stroke="#888" stroke-width="1.5"/><circle cx="6" cy="6" r="2" fill="#888"/></svg>Step 3</span>
  </div>
  <h3 class="abs">Finibus Bonorum et Malorum</h3>
  <div class="abs copy">
    <p>Lorem ipsum dolor sit amet, consectetur adipisicing elit. Temporibus illo vero cupiditate, sed enim voluptatibus provident consectetur.</p>
    <p>Blanditiis aspernatur, non quasi, maxime corporis officiis quia. Cupiditate, voluptatibus ducimus, natus, labore mollitia dolorem incidunt voluptatum, delectus eius git porro placeat animi voluptatem autem hic eligendi sint.</p>
    <ul class="ticks">
      <li><svg width="14" height="14" viewBox="0 0 14 14"><circle cx="7" cy="7" r="7" fill="#2b8ad3"/><path d="M3.8 7.2l2.2 2.2 4.2-4.4" fill="none" stroke="#fff" stroke-width="1.6"/></svg>We are here to support you</li>
      <li><svg width="14" height="14" viewBox="0 0 14 14"><circle cx="7" cy="7" r="7" fill="#2b8ad3"/><path d="M3.8 7.2l2.2 2.2 4.2-4.4" fill="none" stroke="#fff" stroke-width="1.6"/></svg>Free updates</li>
      <li><svg width="14" height="14" viewBox="0 0 14 14"><circle cx="7" cy="7" r="7" fill="#2b8ad3"/><path d="M3.8 7.2l2.2 2.2 4.2-4.4" fill="none" stroke="#fff" stroke-width="1.6"/></svg>Unlimited options and variations</li>
    </ul>
    <a class="read-more" style="display:block;margin-top:14px">READ MORE &gt;&gt;</a>
  </div>
  <div class="abs video" role="img" aria-label="Video still of a business person touching a digital interface">
    <div class="bar"><span>Marrowind IT Consultancy...</span>
      <span style="display:flex;gap:14px;align-items:center"><svg width="16" height="16" viewBox="0 0 16 16"><circle cx="8" cy="8" r="6.5" fill="none" stroke="#fff" stroke-width="1.6"/><path d="M8 4v4l3 2" fill="none" stroke="#fff" stroke-width="1.6"/></svg><svg width="16" height="14" viewBox="0 0 16 14"><path d="M9 1l6 5-6 5V8C5 8 2 9 1 13 1 7 4 4 9 4z" fill="#fff"/></svg></span></div>
    <div class="play"><svg width="20" height="22" viewBox="0 0 20 22"><path d="M2 1l17 10L2 21z" fill="#fff"/></svg></div>
  </div>
</section>

<section class="abs quote-band" role="img" aria-label="Blurred data centre server racks">
  <div class="abs avatar" role="img" aria-label="Client portrait"></div>
  <div class="abs who">Just Perfect</div>
  <blockquote class="abs">" Lorem ipsum dolor sit amet, consectetur adipisicing elit, sed do eiusmod tempor incididunt ut labore et dolore magna aliqua. Ut enim ad minim veniam, quis nostrud exercitation ullamco laboris nisi ut aliquip ex ea commodo consequat. "</blockquote>
  <cite class="abs">- John Doe</cite>
</section>

<section class="why">
  <h2 class="abs" style="left:97px">Why Choose Us</h2>
  <p class="abs intro">Temporibus autem quibusdam et aut officiis debitis aut rerum necessitatibus saepe eveniet ut et voluptates repudiandae sint et molestiae.</p>
  <ul class="abs ticks">
    <li><svg width="14" height="14" viewBox="0 0 14 14"><circle cx="7" cy="7" r="7" fill="#2b8ad3"/><path d="M3.8 7.2l2.2 2.2 4.2-4.4" fill="none" stroke="#fff" stroke-width="1.6"/></svg>Blanditiis praesentium voluptatum deleniti atque corrupti quos</li>
    <li><svg width="14" height="14" viewBox="0 0 14 14"><circle cx="7" cy="7" r="7" fill="#2b8ad3"/><path d="M3.8 7.2l2.2 2.2 4.2-4.4" fill="none" stroke="#fff" stroke-width="1.6"/></svg>Sed ut perspiciatis unde omnis iste natus error sit voluptatem accusanti</li>
    <li><svg width="14" height="14" viewBox="0 0 14 14"><circle cx="7" cy="7" r="7" fill="#2b8ad3"/><path d="M3.8 7.2l2.2 2.2 4.2-4.4" fill="none" stroke="#fff" stroke-width="1.6"/></svg>But I must explain to you how all this mistaken idea of denouncing</li>
    <li><svg width="14" height="14" viewBox="0 0 14 14"><circle cx="7" cy="7" r="7" fill="#2b8ad3"/><path d="M3.8 7.2l2.2 2.2 4.2-4.4" fill="none" stroke="#fff" stroke-width="1.6"/></svg>Nemo enim ipsam voluptatem quia voluptas sit aspernatur</li>
    <li><svg width="14" height="14" viewBox="0 0 14 14"><circle cx="7" cy="7" r="7" fill="#2b8ad3"/><path d="M3.8 7.2l2.2 2.2 4.2-4.4" fill="none" stroke="#fff" stroke-width="1.6"/></svg>At vero eos et accusamus et iusto odio dignissimos ducimus qui</li>
    <li><svg width="14" height="14" viewBox="0 0 14 14"><circle cx="7" cy="7" r="7" fill="#2b8ad3"/><path d="M3.8 7.2l2.2 2.2 4.2-4.4" fill="none" stroke="#fff" stroke-width="1.6"/></svg>Nam libero tempore, cum soluta nobis est eligendi optio cumque nihil</li>
  </ul>
  <a class="abs read-more" style="left:97px;top:2986px">READ MORE &gt;&gt;</a>
</section>

<section class="news">
  <h2 class="abs" style="left:587px">Our News</h2>
  <article class="abs news-item" style="top:2682px">
    <div class="ph" style="background:linear-gradient(135deg,#9aa9b6,#4c5f72 55%,#2a3744)" role="img" aria-label="Business people reviewing documents at a desk"></div>
    <h4>At vero eos et accusamus et iusto odiodig nissimos ducimus qui bland</h4>
    <div class="meta"><span><svg width="10" height="10" viewBox="0 0 10 10"><rect x="0" y="1" width="10" height="9" fill="#2b8ad3"/><rect x="1" y="4" width="8" height="5" fill="#fff"/></svg>15/10/2015</span><span><svg width="10" height="10" viewBox="0 0 10 10"><circle cx="5" cy="3" r="2.5" fill="#2b8ad3"/><path d="M0 10c0-4 10-4 10 0z" fill="#2b8ad3"/></svg>John Doe</span><span><svg width="11" height="10" viewBox="0 0 11 10"><path d="M1 1h9v6H5l-3 2V7H1z" fill="#2b8ad3"/></svg>4 Comments</span></div>
    <p>Duis aute irure dolor in reprehenderit in voluptate velit esse cillum dolore eu fugiat nulla pariatur.</p>
  </article>
  <div class="abs rule" style="top:2818px"></div>
  <article class="abs news-item" style="top:2841px">
    <div class="ph" style="background:linear-gradient(135deg,#e3eef6,#8cbbdd 55%,#3d7fb3)" role="img" aria-label="Hands working with charts on a tablet"></div>
    <h4>At vero eos et accusamus et iusto odiodig nissimos ducimus qui bland</h4>
    <div class="meta"><span><svg width="10" height="10" viewBox="0 0 10 10"><rect x="0" y="1" width="10" height="9" fill="#2b8ad3"/><rect x="1" y="4" width="8" height="5" fill="#fff"/></svg>15/10/2015</span><span><svg width="10" height="10" viewBox="0 0 10 10"><circle cx="5" cy="3" r="2.5" fill="#2b8ad3"/><path d="M0 10c0-4 10-4 10 0z" fill="#2b8ad3"/></svg>John Doe</span><span><svg width="11" height="10" viewBox="0 0 11 10"><path d="M1 1h9v6H5l-3 2V7H1z" fill="#2b8ad3"/></svg>4 Comments</span></div>
    <p>Duis aute irure dolor in reprehenderit in voluptate velit esse cillum dolore eu fugiat nulla pariatur.</p>
  </article>
  <div class="abs rule" style="top:2972px"></div>
  <a class="abs read-more" style="left:587px;top:2986px">VIEW MORE &gt;&gt;</a>
</section>

<footer class="abs footer">
  <div class="abs brand"><div class="logo-name">Marrowind</div><div class="logo-sub">IT Consultancy</div></div>
  <p class="abs about">Lorem ipsum dolor sit amet, consectetur adipisicing elit. Necessitatibus illo vel dolorum soluta consectetur doloribus sit. Delectus non tenetur odit dicta vitae debitis suscipit doloribus. Lorem ipsum dolor sit amet, consectetur adipisicing elit vitae quia dicta.</p>
  <div class="abs reach">
    <span><svg width="9" height="12" viewBox="0 0 9 12"><path d="M4.5 0A4.5 4.5 0 000 4.5C0 8 4.5 12 4.5 12S9 8 9 4.5A4.5 4.5 0 004.5 0z" fill="#fff"/><circle cx="4.5" cy="4.5" r="1.6" fill="#142a40"/></svg>Nine Harbour Lane, 54100</span><i></i>
    <span><svg width="11" height="11" viewBox="0 0 12 12"><path d="M2 1l2.5 0 1 3-1.5 1c.7 1.5 1.5 2.3 3 3l1-1.5 3 1V10c0 .6-.5 1-1 1C5 11 1 7 1 2c0-.5.4-1 1-1z" fill="#fff"/></svg>+1 888 888 888</span><i></i>
    <span><svg width="12" height="9" viewBox="0 0 11 9"><rect x=".5" y=".5" width="10" height="8" fill="none" stroke="#fff"/><path d="M.5 .5l5 4 5-4" fill="none" stroke="#fff"/></svg>info@marrowindconsultancy.com</span>
  </div>
  <div class="abs circles">
    <span></span><span></span><span></span><span></span><span></span>
    <span><svg width="14" height="11" viewBox="0 0 11 9"><rect x=".5" y=".5" width="10" height="8" fill="#fff"/><path d="M.5 .5l5 4 5-4" fill="none" stroke="#142a40"/></svg></span>
  </div>
  <h3 class="abs">Contact Us</h3>
  <div class="abs field" style="top:85px;height:33px">Name <svg width="12" height="12" viewBox="0 0 10 10"><circle cx="5" cy="3" r="2.5" fill="#fff"/><path d="M0 10c0-4 10-4 10 0z" fill="#fff"/></svg></div>
  <div class="abs field" style="top:129px;height:31px">Email <svg width="13" height="10" viewBox="0 0 11 9"><rect x=".5" y=".5" width="10" height="8" fill="#fff"/><path d="M.5 .5l5 4 5-4" fill="none" stroke="#223d59"/></svg></div>
  <div class="abs field" style="top:173px;height:79px;align-items:flex-start">Message <svg width="12" height="12" viewBox="0 0 12 12"><path d="M1 11l1-3 7-7 2 2-7 7z" fill="#fff"/></svg></div>
  <div class="abs send">SEND</div>
</footer>

<div class="abs copyright">Copyright © 2016, Marrowind IT Consultancy. All Rights Reserved</div>

</body>
</html>
```